Existing Website Requiring new Pages

I have an existing word press website that was built using elementor.
Website: www.tallowcrestcare.com.au
I require the Vacancies page (https://www.tallowcrestcare.com.au/vacancies/) to be modified to display our new properties along with minor tweaks to how the information is presented.
The vacancies to be displayed are the exactly the same as those that are located on the homepage of QMR website (https://qmr.org.au/)
The new pages that link off the Vacancies tab will require custom design.
There are roughly 8 pages/properties to be incorporated. i wish for the design to be very similar to that displayed in the following link; https://www.polunda.com.au/vacancies/merrylands
Along with this the back end has not been updated for the last 3 years so it also requires some maintenance.
Website is in the disability industry and the custom pages will display information relative to Property Vacancies.
I have attached a ZIP file with some design guides, the information for each of the properties (which will need to be modified to show our business name Tallowcrest Care) and the example of how it is to look based off the Polunda website.
If you guys have any suggestions or ideas on how to make this more presentable or possible i'm open to your ideas.
Target Market(s)
People looking for SDA properties custom built for people with a disability
Industry/Entity Type
Disability
Coding
Coded - Design and coding required
Number of Pages Required
5+ page

```html
<!DOCTYPE html>
<html lang="en">
<head>
<meta charset="utf-8">
<title>Vacancies | Tallowcrest Care</title>
<link rel="stylesheet" href="https://fonts.googleapis.com/css2?family=Montserrat:wght@400;500;600&family=Roboto:wght@300;400;500&display=swap">
<style>
  :root{
    --ink:#1f1f1f;
    --nav:#333333;
    --accent:#f0845c;
    --brand:#d9479b;
    --muted:#8a8a8a;
    --rule:#dddddd;
    --blue:#1e8fd6;
    --footer-bg:#f7f7f7;
    --bar-bg:#222222;
    --white:#ffffff;
    --social:#2b3a67;
  }
  *{box-sizing:border-box;margin:0;padding:0}
  html,body{width:800px;height:1200px;overflow:hidden;background:var(--white)}
  body{position:relative;font-family:"Roboto",sans-serif;color:var(--ink)}

  .site-header{position:absolute;left:0;top:0;width:800px;height:98px;background:var(--white)}
  .brand{position:absolute;left:73px;top:34px;display:flex;align-items:center;gap:6px;
    font-family:"Montserrat",sans-serif;font-weight:600;font-size:14px;color:var(--brand)}
  .brand-dot{width:12px;height:12px;border-radius:50%;background:var(--brand)}
  .main-nav{position:absolute;right:68px;top:40px;display:flex;gap:16px;
    font-family:"Montserrat",sans-serif;font-weight:600;font-size:7px;letter-spacing:.6px;color:var(--nav)}
  .main-nav .active{color:var(--accent)}

  .hero{position:absolute;left:0;top:98px;width:800px;height:350px;
    background:linear-gradient(90deg,#aeb3b2 0%,#c9cccb 40%,#e6e7e6 60%,#d8d9d8 100%)}
  .hero-title{position:absolute;left:81px;top:130px;font-size:52px;font-weight:400;color:var(--white);letter-spacing:.5px}

  .property-grid{position:absolute;left:73px;top:490px;width:656px;display:grid;
    grid-template-columns:repeat(4,156px);column-gap:11px;row-gap:13px}
  .property-card{height:212px;background:var(--white);border-radius:4px;overflow:hidden;
    box-shadow:0 2px 8px rgba(0,0,0,.08)}
  .property-photo{height:151px}
  .property-body{padding:12px 16px}
  .property-name{font-size:11.5px;font-weight:500;color:var(--ink)}
  .property-type{margin-top:3px;font-size:9px;font-weight:300;color:#444}

  .site-footer{position:absolute;left:0;top:966px;width:800px;height:194px;background:var(--footer-bg)}
  .footer-brand{position:absolute;left:89px;top:62px;display:flex;align-items:center;gap:6px;
    font-family:"Montserrat",sans-serif;font-weight:600;font-size:14px;color:var(--brand)}
  .contact-list{position:absolute;left:86px;top:134px;list-style:none;font-family:"Montserrat",sans-serif;
    font-size:8px;color:var(--muted);line-height:15px}
  .contact-list li{display:flex;align-items:center;gap:6px}
  .contact-list svg{width:9px;height:9px}
  .socials{position:absolute;left:364px;top:37px;display:flex;flex-direction:column;gap:5px}
  .socials span{width:22px;height:22px;border-radius:50%;background:var(--social);display:block}
  .socials .listing{background:#6b2d83}
  .footer-col{position:absolute;top:30px;width:154px;font-family:"Montserrat",sans-serif}
  .footer-col h3{font-size:9.5px;font-weight:500;letter-spacing:.4px;color:var(--ink);
    border-left:2px solid var(--blue);padding-left:8px;line-height:10px;margin-bottom:10px}
  .footer-col ul{list-style:none}
  .footer-col li{font-size:8px;color:var(--muted);line-height:15px;padding:3px 0;border-top:1px solid var(--rule)}
  .footer-col li:last-child{border-bottom:1px solid var(--rule)}
  .col-accommodation{left:426px}
  .col-services{left:596px}

  .copyright-bar{position:absolute;left:0;top:1160px;width:800px;height:40px;background:var(--bar-bg);
    font-family:"Montserrat",sans-serif;font-size:6.5px;color:#cfcfcf;text-align:center;line-height:40px}
</style>
</head>
<body>
  <header class="site-header">
    <div class="brand"><span class="brand-dot"></span>Tallowcrest Care</div>
    <nav class="main-nav">
      <span>HOME</span><span>ABOUT US</span><span class="active">WHAT WE DO ⌄</span>
      <span>REFERRALS</span><span>FEEDBACK</span><span>CONTACT US</span>
    </nav>
  </header>

  <section class="hero" role="img" aria-label="Smiling woman in a wheelchair holding a tablet in a bright room with plants">
    <h1 class="hero-title">Vacancies</h1>
  </section>

  <main class="property-grid">
    <article class="property-card"><div class="property-photo" role="img" aria-label="Penrith house with garage and driveway" style="background:linear-gradient(180deg,#d9dde6,#8d8b80 60%,#6d7c52)"></div><div class="property-body"><h2 class="property-name">Penrith</h2><p class="property-type">4 Bedroom SIL Home</p></div></article>
    <article class="property-card"><div class="property-photo" role="img" aria-label="Mount Druitt brick house with paved driveway" style="background:linear-gradient(180deg,#a86a52,#5c7d3a 50%,#c98a72)"></div><div class="property-body"><h2 class="property-name">Mount Druitt</h2><p class="property-type">4 Bedroom SIL Home</p></div></article>
    <article class="property-card"><div class="property-photo" role="img" aria-label="Casula cream house with hedge and lawn" style="background:linear-gradient(180deg,#5fa3e0,#e6d6b0 50%,#8aa060)"></div><div class="property-body"><h2 class="property-name">Casula</h2><p class="property-type">4 Bedroom SIL Home</p></div></article>
    <article class="property-card"><div class="property-photo" role="img" aria-label="Eastwood cottage with blue shutters" style="background:linear-gradient(180deg,#dcd0bf,#d6c6b0 60%,#7c9a4e)"></div><div class="property-body"><h2 class="property-name">Eastwood</h2><p class="property-type">4 Bedroom SIL Home</p></div></article>
    <article class="property-card"><div class="property-photo" role="img" aria-label="Baulkham Hills brick home with palm tree" style="background:linear-gradient(180deg,#6fb3e8,#c8a77e 50%,#4f9a3a)"></div><div class="property-body"><h2 class="property-name">Baulkham Hills</h2><p class="property-type">4 Bedroom SIL Home</p></div></article>
    <article class="property-card"><div class="property-photo" role="img" aria-label="Merrylands orange brick home with driveway" style="background:linear-gradient(180deg,#7cb6e6,#c9703e 45%,#5a9c3c 75%,#c8c8c4)"></div><div class="property-body"><h2 class="property-name">Merrylands</h2><p class="property-type">4 Bedroom SIL Home</p></div></article>
    <article class="property-card"><div class="property-photo" role="img" aria-label="Alexandria grey two-storey house" style="background:linear-gradient(180deg,#8fc0ea,#7a8290 50%,#5c9c3a)"></div><div class="property-body"><h2 class="property-name">Alexandria</h2><p class="property-type">4 Bedroom SIL Home</p></div></article>
    <article class="property-card"><div class="property-photo" role="img" aria-label="Barangaroo two-storey house with double garage" style="background:linear-gradient(180deg,#7fb4e2,#8a7c68 50%,#5d9e3d)"></div><div class="property-body"><h2 class="property-name">Barangaroo</h2><p class="property-type">4 Bedroom SIL Home</p></div></article>
  </main>

  <footer class="site-footer">
    <div class="footer-brand"><span class="brand-dot"></span>Tallowcrest Care</div>
    <ul class="contact-list">
      <li><svg viewBox="0 0 10 10"><rect x="1" y="2" width="8" height="6" fill="none" stroke="#e0477f"/><path d="M1 2l4 3 4-3" fill="none" stroke="#e0477f"/></svg>Email: info@tallowcrestcare.com.au</li>
      <li><svg viewBox="0 0 10 10"><path d="M2 1l2 2-1 1.5c.8 1.5 1.5 2.2 3 3L7.5 6l2 2-1.5 1.5C4.5 9 1 5.5.5 2z" fill="#e0477f"/></svg>Phone: +61 0400 318 562</li>
      <li><svg viewBox="0 0 10 10"><circle cx="5" cy="5" r="4" fill="none" stroke="#e0477f"/><path d="M5 2.5V5l2 1" fill="none" stroke="#e0477f"/></svg>Operating Hours: 9AM To 5PM Monday - Friday</li>
    </ul>
    <div class="socials"><span class="listing"></span><span></span><span style="background:#222"></span><span style="background:#1c6fb0"></span></div>
    <div class="footer-col col-accommodation">
      <h3>ACCOMMODATION</h3>
      <ul>
        <li>Supported Independent Living (SIL)</li>
        <li>Specialist Disability<br>Accommodation (SDA)</li>
        <li>Short term Accommodation<br>(Respite)</li>
        <li>Vacancies</li>
      </ul>
    </div>
    <div class="footer-col col-services">
      <h3>WHAT WE DO</h3>
      <ul>
        <li>In Home Care</li>
        <li>Social &amp; Community Services</li>
        <li>Therapeutic Supports</li>
        <li>Support Coordination</li>
        <li>Home Modifications</li>
      </ul>
    </div>
  </footer>

  <div class="copyright-bar">© Copyright 2021 | Tallowcrest Care | All Rights Reserved.</div>
</body>
</html>
```